RW Framewell Inc Business cards

We need business cards using our existing logo but slightly modified. Right now the logo says RW Loadbearing Masonry. We want to keep the RW part of the design, but replace the Structural Concrete portion with "FRAMEWELL". Please see the attached file.
Ideally this would be a blank template so we can add Different Names, titles, and phone numbers later.
On the one side we want only the logo and on the other side the detail. I'm attaching an example for you to see.
Please reach out with any other questions. Our address and other details will be given out once we find a design we like.

Target Market(s)

Construction Industry

```html
<!DOCTYPE html>
<html lang="en">
<head>
<meta charset="utf-8">
<title>RW Framewell Inc — Business Cards</title>
<link rel="stylesheet" href="https://fonts.googleapis.com/css2?family=Montserrat:wght@600;700&family=Roboto:wght@400;500&display=swap">
<style>
  :root {
    --bg: #c9c9c9;
    --card: #f7f7f5;
    --brand-blue: #2f5fa7;
    --brand-grey: #6b6b6b;
    --text: #555555;
    --rule: #4a6fb0;
  }
  * { box-sizing: border-box; margin: 0; padding: 0; }
  html, body { width: 1200px; height: 852px; overflow: hidden; }
  body { background: var(--bg); position: relative; font-family: "Roboto", Arial, sans-serif; }

  .card {
    position: absolute;
    width: 500px; height: 286px;
    background: var(--card);
    border-radius: 18px;
    overflow: hidden;
    box-shadow: 0 6px 14px rgba(0,0,0,.18);
  }

  /* Front: logo only */
  .card--front { left: 90px; top: 110px; }
  .card--front .edge-band {
    position: absolute; left: 0; right: 0; bottom: 0; height: 10px;
    display: flex;
  }
  .edge-band .grey { flex: 0 0 45%; background: var(--brand-grey); }
  .edge-band .blue { flex: 1; background: var(--brand-blue); }
  .front-wordmark {
    position: absolute; left: 0; right: 0; top: 96px;
    text-align: center;
    font-family: "Montserrat", Arial, sans-serif; font-weight: 700;
    color: var(--brand-blue);
    line-height: 1;
  }
  .front-wordmark .initials { display: block; font-size: 64px; letter-spacing: 2px; }
  .front-wordmark .name { display: block; font-size: 22px; letter-spacing: 7px; margin-top: 8px; }

  /* Back: details */
  .card--back { left: 610px; top: 456px; }
  .back-wordmark {
    position: absolute; right: 40px; top: 34px;
    text-align: right;
    font-family: "Montserrat", Arial, sans-serif; font-weight: 700;
    color: var(--brand-blue); line-height: 1;
  }
  .back-wordmark .initials { display: block; font-size: 44px; letter-spacing: 2px; }
  .back-wordmark .name { display: block; font-size: 15px; letter-spacing: 5px; margin-top: 6px; }

  .divider {
    position: absolute; left: 40px; right: 40px; top: 146px;
    height: 1px; background: var(--rule);
  }
  .address {
    position: absolute; right: 40px; top: 156px;
    text-align: right; font-size: 12px; line-height: 1.4; color: var(--text);
  }
  .edge-dot {
    position: absolute; left: -22px; top: 150px;
    width: 40px; height: 40px; border-radius: 50%;
    background: var(--brand-blue);
  }
  .person { position: absolute; left: 40px; top: 150px; }
  .person .full-name {
    font-family: "Montserrat", Arial, sans-serif; font-weight: 700;
    font-size: 17px; color: var(--brand-blue);
  }
  .person .role { font-size: 12px; color: var(--text); margin-top: 2px; }

  .contacts { position: absolute; left: 40px; top: 206px; list-style: none; }
  .contacts li {
    display: flex; align-items: center; gap: 10px;
    font-size: 12.5px; color: var(--text); line-height: 20px;
  }
  .contacts svg { width: 11px; height: 11px; fill: var(--brand-blue); flex: none; }
</style>
</head>
<body>

  <section class="card card--front" aria-label="Card front">
    <div class="front-wordmark">
      <span class="initials">RW</span>
      <span class="name">FRAMEWELL</span>
    </div>
    <div class="edge-band"><span class="grey"></span><span class="blue"></span></div>
  </section>

  <section class="card card--back" aria-label="Card back">
    <div class="back-wordmark">
      <span class="initials">RW</span>
      <span class="name">FRAMEWELL</span>
    </div>
    <div class="divider"></div>
    <p class="address">18 Quarry Lane, Millbrook,<br>Oregon, US 97001</p>
    <span class="edge-dot"></span>
    <div class="person">
      <p class="full-name">Daniel Marsh</p>
      <p class="role">Managing Director</p>
    </div>
    <ul class="contacts">
      <li>
        <svg viewBox="0 0 24 24" aria-hidden="true"><path d="M6.6 10.8a15 15 0 0 0 6.6 6.6l2.2-2.2a1 1 0 0 1 1-.25 11.4 11.4 0 0 0 3.6.57 1 1 0 0 1 1 1V20a1 1 0 0 1-1 1A17 17 0 0 1 3 4a1 1 0 0 1 1-1h3.5a1 1 0 0 1 1 1c0 1.25.2 2.45.57 3.57a1 1 0 0 1-.25 1z"/></svg>
        555-014-2290
      </li>
      <li>
        <svg viewBox="0 0 24 24" aria-hidden="true"><path d="M2 5h20v14H2z M2 5l10 8 10-8" stroke="#f7f7f5" stroke-width="1.5"/></svg>
        daniel@framewellinc.com
      </li>
      <li>
        <svg viewBox="0 0 24 24" aria-hidden="true"><circle cx="12" cy="12" r="10"/><path d="M2 12h20M12 2c3 3 3 17 0 20M12 2c-3 3-3 17 0 20" stroke="#f7f7f5" stroke-width="1.5" fill="none"/></svg>
        www.framewellinc.com
      </li>
    </ul>
  </section>

</body>
</html>
```